Website Redesign

This is a B2B (Mainly)/B2C website .

Vaporel (our manufacturer) only sells the Sprayer itself. As a result they rarely speak directly to the benefits of a disinfecting chemicals ie. Their marketing is more directed to how quickly the sprayer can cover a given area or how much disinfecting Chemical is saved by spraying instead of the 'spray and wipe method. Also how much labor is saved by spraying.

We will be selling both similar to brindlowash.com

1. Main Selling Point? Infectious disease control and prevention via Electromagnetic Disinfecting Sprayers. Upsell is chemicals used in the sprayer and other products for use in disinfection and cleaning.

Our price point is $1495 so sales generally happen after they speak to our sales team.

End user is in most cases a Business. In some cases an individual as well but 75% business, hospital, School district, Universities.

Redesign is meant to tell a much better story to customer by and presenting a cleaner design. Most important metric is increased conversions.

Number of Pages Required

5+ page

```html
<!DOCTYPE html>
<html lang="en">
<head>
<meta charset="utf-8">
<title>KRV Group — Disinfecting Sprayers</title>
<link href="https://fonts.googleapis.com/css2?family=Oswald:wght@300;400;500&family=Montserrat:ital,wght@0,400;0,500;0,600;0,700;1,400&display=swap" rel="stylesheet">
<style>
:root{
  --teal:#1ba8c4;
  --teal-light:#8fdcea;
  --navy:#0c3d63;
  --navy-deep:#0a2f55;
  --ocean:#0e5c7d;
  --ink:#1d2a33;
  --text:#5f6a72;
  --paper:#ffffff;
  --mist:#f3f3f3;
  --line:#d7dde1;
}
*{margin:0;padding:0;box-sizing:border-box}
html,body{width:1200px;height:4992px;overflow:hidden}
body{position:relative;background:var(--paper);font-family:"Montserrat",sans-serif;color:var(--text)}
.abs{position:absolute}
.heading{font-family:"Oswald",sans-serif;text-transform:uppercase;text-align:center;letter-spacing:-.5px}
.heading .accent{color:var(--teal);font-weight:500}
.heading .light{font-weight:300;color:var(--ink)}
.btn{position:absolute;display:flex;align-items:center;justify-content:center;gap:8px;background:var(--teal);color:#fff;font-weight:700;font-size:13px;letter-spacing:.3px;text-transform:uppercase}
.btn .arrow{width:12px;height:12px;border-radius:50%;background:#fff;position:relative}
.btn .arrow::after{content:"";position:absolute;left:3px;top:3px;border-left:6px solid var(--teal);border-top:3px solid transparent;border-bottom:3px solid transparent}
.mark-dot{position:absolute;width:56px;height:56px;border-radius:50%;background:var(--teal-light)}
/* top bar */
.news-bar{top:0;left:0;width:1200px;height:37px;background:var(--navy)}
.news-label{top:0;left:0;width:397px;height:37px;background:var(--teal);clip-path:polygon(0 0,100% 0,94% 100%,0 100%);color:#fff;font-weight:700;font-size:17px;padding:8px 0 0 182px}
.news-text{top:10px;left:478px;color:#fff;font-size:12px}
/* header */
.site-header{top:37px;left:0;width:1200px;height:83px;background:#fff}
.brand{display:flex;align-items:center;gap:14px;font-weight:500;font-size:34px;color:var(--ink)}
.brand .dot{width:54px;height:54px;border-radius:50%;background:var(--teal-light)}
.site-header .brand{position:absolute;left:145px;top:14px}
.main-nav{position:absolute;right:144px;top:34px;display:flex;gap:30px;font-size:14px;color:var(--ink);text-transform:uppercase}
.main-nav .current{position:relative}
.main-nav .current::after{content:"";position:absolute;left:0;right:0;top:48px;height:3px;background:var(--teal)}
/* hero */
.hero{top:120px;left:0;width:1200px;height:626px;background:linear-gradient(110deg,#0e2e5c,#18508a 55%,#123e6f);clip-path:polygon(0 0,100% 0,100% 96%,0 100%)}
.hero-visual{top:190px;left:60px;width:495px;height:495px;border-radius:50%;background:radial-gradient(circle,#6fa6d6 0%,#2f6aa8 45%,rgba(24,80,138,0) 70%)}
.hero-wedge{top:636px;left:930px;width:270px;height:85px;background:var(--teal);clip-path:polygon(0 54%,100% 0,100% 100%)}
.hero-title{top:225px;left:593px;font-family:"Oswald",sans-serif;font-weight:500;font-size:104px;line-height:1;color:#fff}
.hero-title span{color:var(--teal)}
.hero-copy{top:370px;left:597px;width:480px;color:#fff;font-size:16.5px;line-height:27px}
.hero-dots{top:609px;left:597px;display:flex;gap:8px}
.hero-dots i{width:10px;height:10px;border-radius:50%;background:#fff}
.hero-dots i.on{background:var(--teal)}
/* welcome */
.intro-copy{left:170px;width:860px;text-align:center;font-size:13.5px;line-height:31px}
.product-range{top:1200px;left:145px;width:910px;height:450px;display:flex;gap:40px}
.product{flex:1;background:linear-gradient(160deg,#e9ebee,#2b2e33 60%,#15171a)}
/* threats */
.threats{top:1690px;left:0;width:1200px;height:694px;background:linear-gradient(180deg,#115f80,#0c4f6e);clip-path:polygon(0 20%,100% 0,100% 100%,0 80%)}
/* services */
.service{position:absolute;width:300px;text-align:center}
.service .icon{width:126px;height:126px;border-radius:50%;border:3px solid var(--teal-light);margin:0 auto;display:flex;align-items:center;justify-content:center}
.service h3{font-size:17px;font-weight:600;color:var(--ink);letter-spacing:1px;text-transform:uppercase;margin-top:34px;line-height:24px}
.service p{font-size:13.5px;line-height:25px;margin-top:14px}
/* case study */
.case-photo{top:3539px;left:0;width:599px;height:686px;background:linear-gradient(180deg,#b9c4cc,#6b7c8a 60%,#3a4a66)}
.case-panel{top:3539px;left:599px;width:601px;height:686px;background:var(--mist)}
.case-quote{top:3843px;left:661px;width:410px;font-style:italic;font-size:13.5px;line-height:29px}
.case-name{top:4008px;left:661px;font-size:14px;font-weight:700;color:var(--ink)}
.case-name em{font-weight:400;color:var(--text);font-size:13px}
/* contact */
.contact{top:4225px;left:0;width:1200px;height:558px;background:var(--ocean)}
.field{position:absolute;background:#fff;font-size:12px;color:var(--ink);padding:14px 16px}
.field.select::after{content:"";position:absolute;right:16px;top:20px;border-top:5px solid var(--ink);border-left:5px solid transparent;border-right:5px solid transparent}
/* footer */
.site-footer .brand{position:absolute;left:145px;top:4830px;font-size:38px;font-weight:600}
.footer-nav{position:absolute;left:535px;top:4836px;display:flex;gap:28px;font-size:14px;font-weight:600;color:var(--ink);text-transform:uppercase}
.legal{top:4880px;left:535px;font-size:11px;color:var(--text)}
.social{top:4930px;left:535px;display:flex;gap:34px}
.social i{width:22px;height:22px;border-radius:50%;background:#9aa4ab}
</style>
</head>
<body>

<div class="abs news-bar"></div>
<div class="abs news-label">IN THE NEWS</div>
<div class="abs news-text">Lorem ipsum dolor sit ametconsectetur adipiscing elited do eiusmod</div>

<header class="abs site-header">
  <div class="brand"><span class="dot"></span>KRV GROUP</div>
  <nav class="main-nav">
    <span class="current">Home</span><span>About Us</span><span>Products</span><span>FAQ</span><span>Pricing</span><span>Contact</span>
  </nav>
</header>

<section>
  <div class="abs hero" role="img" aria-label="Dark blue backdrop of microscopic virus particles"></div>
  <div class="abs hero-visual" role="img" aria-label="Close-up illustration of a virus particle"></div>
  <div class="abs hero-wedge"></div>
  <h1 class="abs hero-title"><span>KRV</span> GROUP</h1>
  <p class="abs hero-copy">Lorem ipsum dolor sit ametonsectetur adipiscing elit sed do eiusmod tpor incididunt ut labore</p>
  <a class="btn" style="top:461px;left:597px;width:153px;height:43px">Get Started <span class="arrow"></span></a>
  <div class="abs hero-dots"><i></i><i></i><i class="on"></i><i></i><i></i></div>
</section>

<section>
  <span class="mark-dot" style="top:775px;left:572px"></span>
  <h2 class="abs heading" style="top:862px;left:0;width:1200px;font-size:58px"><span class="accent">Welcome to</span> <span class="light">KRV Group</span></h2>
  <p class="abs intro-copy" style="top:966px">Lorem ipsum dolor sit amet, consectetur adipiscing elit, sed do eiusmod tempor incididunt ut labore et dolore magna aliqua. Quis ipsum suspendisse ultrices gravida. Risus commodo viverra maecenas accumsan lacus vel facilisiorem ipsum dolor sit amet, consectetur adipiscing elit, sed do eiusmod tempor incididunt ut labore et dolore magna aliqua. Quis ipsum suspendisse ultrices gravida. Risus commodo viverra maecenas accumsan lacus vel facilisis.rem ipsum dolor sit amet, consectetur adipiscing elit, sed do eiusmod tempor incididunt ut labore</p>
  <div class="abs product-range">
    <div class="product" role="img" aria-label="Handheld electrostatic disinfecting sprayer"></div>
    <div class="product" role="img" aria-label="Wheeled cart disinfecting sprayer"></div>
    <div class="product" role="img" aria-label="Backpack disinfecting sprayer"></div>
  </div>
</section>

<section>
  <div class="abs threats" role="img" aria-label="Workers in protective suits disinfecting a station, tinted teal"></div>
  <h2 class="abs heading" style="top:1862px;left:0;width:1200px;font-size:40px;line-height:52px;color:#fff;font-weight:500">Serious threats to public health and<br>our nation’s economy</h2>
  <p class="abs intro-copy" style="top:2005px;left:200px;width:800px;color:#e3eef3">Lorem ipsum dolor sit amet, consectetur adipiscing elit, sed do eiusmod tempor incididunt ut labore et dolore magna alis ipsum suspendisse ultrices gravis commodo viverra maecenas accumsan lacus vel facilisis. Lorem ipsum dolor sit amet, consectetur adipiscing elit, sed do eiusmod tempor incididunt ut labore et dolore magna aliqua. Quis ipsum suspendisse ultricesmmodo viverra maecenas accumsan lacus vel facilisis.</p>
  <a class="btn" style="top:2168px;left:523px;width:153px;height:42px">Get Started <span class="arrow"></span></a>
</section>

<section>
  <span class="mark-dot" style="top:2398px;left:572px"></span>
  <h2 class="abs heading" style="top:2490px;left:0;width:1200px;font-size:58px;line-height:66px"><span class="accent">Already at work</span><br><span class="light">In leading institutions</span></h2>

  <div class="service" style="left:116px;top:2703px">
    <div class="icon"><svg width="60" height="60" viewBox="0 0 60 60" fill="none" stroke="#0c3d63" stroke-width="2"><path d="M8 34l12-8h12l-4 6h-8M52 26l-12 8H28"/><path d="M30 22c-3-4-9-1-6 4l6 5 6-5c3-5-3-8-6-4z"/></svg></div>
    <h3>Healthcare</h3>
    <p>Lorem ipsum dolor sit amet,<br>consectetur adipiscing elit, sed do<br>eiusmod tempor incididunt</p>
  </div>
  <div class="service" style="left:450px;top:2703px">
    <div class="icon"><svg width="60" height="60" viewBox="0 0 60 60" fill="none" stroke="#0c3d63" stroke-width="2"><rect x="18" y="14" width="14" height="36"/><rect x="32" y="24" width="12" height="26"/><path d="M12 50h38M22 20h6M22 28h6M22 36h6M36 30h4M36 38h4"/></svg></div>
    <h3>Building Services<br>Contractors</h3>
    <p>Lorem ipsum dolor sit amet,<br>consectetur adipiscing elit.</p>
  </div>
  <div class="service" style="left:784px;top:2703px">
    <div class="icon"><svg width="60" height="60" viewBox="0 0 60 60" fill="none" stroke="#0c3d63" stroke-width="2"><circle cx="30" cy="30" r="20"/><circle cx="30" cy="30" r="13"/><path d="M25 22v16M35 22v16"/></svg></div>
    <h3>Food Services</h3>
    <p>Lorem ipsum dolor sit amet,<br>consectetur adipiscing elit, sed do<br>eiusmod tempor incididunt</p>
  </div>
  <div class="service" style="left:284px;top:3045px">
    <div class="icon"><svg width="60" height="60" viewBox="0 0 60 60" fill="none" stroke="#0c3d63" stroke-width="2"><path d="M8 24l22-10 22 10-22 10z"/><path d="M18 29v10c6 5 18 5 24 0V29M50 25v12"/></svg></div>
    <h3>Education</h3>
    <p>Lorem ipsum dolor sit amet,<br>consectetur adipiscing elit, sed do<br>eiusmod tempor incididunt</p>
  </div>
  <div class="service" style="left:618px;top:3045px">
    <div class="icon"><svg width="60" height="60" viewBox="0 0 60 60" fill="none" stroke="#0c3d63" stroke-width="2"><circle cx="40" cy="38" r="8"/><path d="M12 50l8-14 10 4M20 36l6-14h10M30 40l-4 12"/></svg></div>
    <h3>Athletics &amp;<br>Professional Sports</h3>
    <p>Lorem ipsum dolor sit amet,<br>consectetur adipiscing elit.</p>
  </div>

  <a class="btn" style="top:3386px;left:486px;width:228px;height:41px">View More Services <span class="arrow"></span></a>
</section>

<section>
  <div class="abs case-photo" role="img" aria-label="Two workers in white protective suits spraying disinfectant in a walkway"></div>
  <div class="abs case-panel"></div>
  <span class="mark-dot" style="top:3626px;left:661px"></span>
  <h2 class="abs heading" style="top:3714px;left:661px;font-size:58px;text-align:left"><span class="accent">Our</span> <span class="light">Case Study</span></h2>
  <p class="abs case-quote">Lorem ipsum dolor sit amet, consectetur adipiscing elit, sed do eiusmod tempor incididunt ut labore et dolore magna aliqpsum suspendisse ultrices grasus commodo viverra maecenas accumsan eur sint occaecat cupidatat non proident, sunt in culpa qui offacus vel facilisis.</p>
  <p class="abs case-name">TALIA VOSS , <em>accumsan eur sint</em></p>
  <a class="btn" style="top:4101px;left:661px;width:244px;height:42px">Read the Case Study <span class="arrow"></span></a>
</section>

<section>
  <div class="abs contact"></div>
  <h2 class="abs heading" style="top:4330px;left:0;width:1200px;font-size:56px"><span class="accent">For more</span> <span class="light" style="color:#fff">Information</span></h2>
  <div class="field" style="top:4444px;left:132px;width:219px;height:44px">Name</div>
  <div class="field" style="top:4444px;left:372px;width:219px;height:44px">Email</div>
  <div class="field" style="top:4444px;left:610px;width:219px;height:44px">Phone</div>
  <div class="field select" style="top:4444px;left:849px;width:219px;height:44px">Address</div>
  <div class="field" style="top:4510px;left:132px;width:936px;height:81px">Message</div>
  <a class="btn" style="top:4630px;left:492px;width:215px;height:39px">Submi Message <span class="arrow"></span></a>
</section>

<footer class="site-footer">
  <div class="brand"><span class="dot"></span>KRV GROUP</div>
  <nav class="footer-nav"><span>Home</span><span>About Us</span><span>Products</span><span>FAQ</span><span>Pricing</span><span>Contact</span></nav>
  <p class="abs legal">Copyrights @ 2020 KRV Group. All Rights Reserved &nbsp;|&nbsp; Privacy Policy</p>
  <div class="abs social"><i></i><i></i><i></i></div>
</footer>

</body>
</html>
```